Book Cover for Productivity Book

I need a book cover for my latest publication "On Momentum: The Gathered Insights of the Swiftest Worker Breathing"

You can see my branding at www.quillmarrow.com

This is meant to be my epic pinaccle work on productivity, I want it to look like the end all be all word on productivity.

Target Market(s)

entrepreneurs

```html
<!DOCTYPE html>
<html lang="en">
<head>
<meta charset="utf-8">
<title>On Momentum – Book Cover</title>
<link rel="stylesheet" href="https://fonts.googleapis.com/css2?family=Bebas+Neue&family=Raleway:wght@500&display=swap">
<style>
  :root {
    --backdrop: #acd1d8;
    --paper: #ececec;
    --crimson: #a00000;
    --ink: #0b1c27;
    --art-light: #ecd24a;
    --art-deep: #c9a400;
  }
  * { margin: 0; padding: 0; box-sizing: border-box; }
  html, body {
    width: 1200px;
    height: 1200px;
    overflow: hidden;
    background: var(--backdrop);
  }
  .canvas {
    position: relative;
    width: 1200px;
    height: 1200px;
  }
  .cover {
    position: absolute;
    left: 226px;
    top: 50px;
    width: 748px;
    height: 1100px;
    background: var(--paper);
    overflow: hidden;
  }
  .cover__kicker {
    position: absolute;
    top: 40px;
    left: 0;
    width: 100%;
    text-align: center;
    font-family: "Bebas Neue", sans-serif;
    font-size: 164px;
    line-height: 1;
    color: var(--crimson);
  }
  .cover__band {
    position: absolute;
    top: 202px;
    left: 0;
    width: 100%;
    height: 175px;
    background: var(--ink);
    display: flex;
    align-items: center;
    justify-content: center;
  }
  .cover__title {
    font-family: "Bebas Neue", sans-serif;
    font-weight: 400;
    font-size: 172px;
    line-height: 1;
    padding-top: 14px;
    color: var(--paper);
    letter-spacing: 2px;
  }
  .cover__subtitle {
    position: absolute;
    top: 396px;
    left: 0;
    width: 100%;
    text-align: center;
    font-family: "Raleway", sans-serif;
    font-weight: 500;
    font-size: 29px;
    line-height: 1.38;
    color: var(--ink);
  }
  .cover__hill {
    position: absolute;
    left: 0;
    top: 0;
    width: 748px;
    height: 1100px;
  }
  .cover__art {
    position: absolute;
    left: 206px;
    top: 506px;
    width: 340px;
    height: 486px;
    border-radius: 24px;
    background: radial-gradient(ellipse at 50% 40%, var(--art-light) 0%, var(--art-deep) 100%);
  }
  .cover__footer {
    position: absolute;
    left: 0;
    bottom: 0;
    width: 100%;
    height: 60px;
    background: var(--ink);
  }
</style>
</head>
<body>
<main class="canvas">
  <section class="cover">
    <svg class="cover__hill" viewBox="0 0 748 1100" aria-hidden="true">
      <path fill="var(--ink)"
            d="M0 636 C120 578 380 560 560 690 C655 760 718 860 748 968 L748 1040 L0 1040 Z"/>
      <path fill="var(--crimson)"
            d="M0 652 C120 594 380 578 556 706 C650 775 712 872 748 988 L748 1040 L0 1040 Z"/>
    </svg>

    <div class="cover__art" role="img"
         aria-label="Illustration of a floating glowing light bulb holding a gear with a stopwatch dial"></div>

    <div class="cover__kicker">On</div>
    <div class="cover__band">
      <h1 class="cover__title">Momentum</h1>
    </div>
    <p class="cover__subtitle">The Gathered Insights of the<br>Swiftest Worker Breathing</p>
    <div class="cover__footer"></div>
  </section>
</main>
</body>
</html>
```